Business Card Design needed for start up company Halvora

In need of a new business card designed for a start up company based in Sydney, Halvora is a new start up innovative Company, our mission it to make property accessible for everyday Australian and to become the leading Real Estate platform in Australia. We want it to be fresh and clean.

Industry/Entity Type

Financial

Contact Information for Business Card

Section for Name
Section for Title

HALVORA - The Strength of Pooling
Mobile:
Direct:

Font styles to use
Sans Serif

Colors
33a6d7
0692cd
0255a3
ffffff

Requirements
Must have
• Logo, all business card details

```html
<!DOCTYPE html>
<html lang="en">
<head>
<meta charset="utf-8">
<title>Halvora Business Card</title>
<link href="https://fonts.googleapis.com/css2?family=Arimo:wght@400;700&display=swap" rel="stylesheet">
<style>
  :root {
    --navy: #1d4274;
    --navy-deep: #193a66;
    --sky: #2793cc;
    --sky-light: #33a6d7;
    --white: #ffffff;
    --paper: #f2f2f2;
    --ink-light: #e6e9ee;
    --stage: #d2d2d2;
  }
  * { margin: 0; padding: 0; box-sizing: border-box; }
  html, body { width: 1200px; height: 965px; overflow: hidden; }
  body {
    background: var(--stage);
    font-family: "Arimo", Arial, sans-serif;
    position: relative;
  }
  .card {
    position: absolute;
    left: 277px;
    width: 648px;
    height: 369px;
    border-radius: 36px;
    overflow: hidden;
  }
  .card-front { top: 97px; background: linear-gradient(#ffffff, #ececec); }
  .card-back { top: 502px; background: linear-gradient(var(--navy), var(--navy-deep)); }
  .card svg.shape { position: absolute; inset: 0; }

  .brand { position: absolute; display: flex; align-items: center; }
  .brand-dot { border-radius: 50%; flex: none; }
  .brand-name { font-weight: 700; letter-spacing: -1px; line-height: 1; }

  .front-brand { left: 48px; top: 44px; gap: 12px; }
  .front-brand .brand-dot { width: 86px; height: 86px; background: var(--sky-light); }
  .front-brand .brand-name { font-size: 56px; color: var(--navy); }

  .person { position: absolute; left: 48px; top: 230px; color: var(--white); }
  .person-name { font-size: 20px; font-weight: 700; }
  .person-title { font-size: 15px; color: var(--ink-light); margin-top: 3px; }

  .address {
    position: absolute; left: 48px; top: 309px;
    font-size: 15px; line-height: 19px; color: var(--ink-light);
  }

  .contacts {
    position: absolute; left: 257px; top: 273px;
    list-style: none; font-size: 15px; line-height: 19px; color: var(--ink-light);
  }
  .contacts li { display: flex; align-items: center; gap: 8px; }
  .contacts svg { width: 15px; height: 15px; flex: none; }

  .back-brand { left: 90px; top: 113px; gap: 20px; }
  .back-brand .brand-dot { width: 142px; height: 142px; background: var(--paper); }
  .back-brand .brand-name { font-size: 66px; color: var(--paper); }

  .back-web {
    position: absolute; left: 0; right: 0; top: 322px;
    text-align: center; font-size: 14px; letter-spacing: 4px; color: var(--ink-light);
  }
</style>
</head>
<body>

<section class="card card-front">
  <svg class="shape" viewBox="0 0 648 369" width="648" height="369" aria-hidden="true">
    <path d="M0,155 C180,180 430,168 648,64 L648,70 C440,172 200,200 0,190 Z" fill="var(--sky)"/>
    <path d="M0,198 C210,206 440,170 648,72 L648,369 L0,369 Z" fill="var(--navy)"/>
  </svg>

  <div class="brand front-brand">
    <span class="brand-dot"></span>
    <span class="brand-name">HALVORA</span>
  </div>

  <div class="person">
    <p class="person-name">Liam Carter</p>
    <p class="person-title">Managing Director</p>
  </div>

  <p class="address">Here your company or<br>home address</p>

  <ul class="contacts">
    <li>
      <svg viewBox="0 0 16 16" aria-hidden="true"><rect x="1" y="2" width="4" height="12" rx="1" fill="#e6e9ee"/><rect x="6" y="3" width="9" height="11" rx="1" fill="none" stroke="#e6e9ee" stroke-width="1.5"/><rect x="8" y="5" width="5" height="2" fill="#e6e9ee"/></svg>
      +61 2 5550 1840
    </li>
    <li>
      <svg viewBox="0 0 16 16" aria-hidden="true"><path d="M3,1 L6,1 L7,5 L5,6.5 C6,9 7,10 9.5,11 L11,9 L15,10 L15,13 C15,14 14,15 13,15 C7,15 1,9 1,3 C1,2 2,1 3,1 Z" fill="#e6e9ee"/></svg>
      +61 4 5550 2291
    </li>
    <li>
      <svg viewBox="0 0 16 16" aria-hidden="true"><rect x="1" y="3.5" width="14" height="9" fill="none" stroke="#e6e9ee" stroke-width="1.5"/><path d="M1,3.5 L8,9 L15,3.5" fill="none" stroke="#e6e9ee" stroke-width="1.5"/></svg>
      info@halvora.com
    </li>
    <li>
      <svg viewBox="0 0 16 16" aria-hidden="true"><circle cx="8" cy="8" r="6.5" fill="none" stroke="#e6e9ee" stroke-width="1.3"/><ellipse cx="8" cy="8" rx="3" ry="6.5" fill="none" stroke="#e6e9ee" stroke-width="1.1"/><path d="M1.5,8 H14.5 M2.5,5 H13.5 M2.5,11 H13.5" stroke="#e6e9ee" stroke-width="1.1"/></svg>
      www.halvora.com
    </li>
  </ul>
</section>

<section class="card card-back">
  <div class="brand back-brand">
    <span class="brand-dot"></span>
    <span class="brand-name">HALVORA</span>
  </div>
  <p class="back-web">www.halvora.com</p>
</section>

</body>
</html>
```